Website Redesign for Existing BBQ Catering Company

Need to get my website (HollowOakSmoke.com) redesigned. Looking for a cleaner look but still patriotic and rustic. Would like to add parallax scrolling on the menu page and include some pics from our photo gallery. Would like to display a picture of the brisket before scrolling into the meat section of our menu and the same for the other sections too.....picture of one of our sides, appetizers, desserts, etc.

Would also like to add three new pages called Corporate Events, Weddings, and Veteran Events possibly in a drop-down menu called Catering. You can use pics from our Facebook page. We've posted tons of pics from weddings that we've done. I've uploaded some corporate and wedding pics but you can pics the ones that look best. I can swap them out later if needed.

Would like to keep it Wordpress if possible so I can update it as needed.

Also need to add some links to our storefront on The Vow Loft. I have the HTML code and will upload the image here.

Also need to add social media links for our Facebook, Instagram and Twitter pages.

The contact form that I'm using now feeds the leads into another site called Tenbrim.com that I use to manage my clients.

Target Market(s)

Weddings, corporate events, veterans

Industry/Entity Type

Catering

Coding

Coded - Design and coding required

Number of Pages Required

5+ page

Colors
ec1f27
3176b5
ffffff

Requirements
Must have
• Really like the hero image design. Looks less like a template. Check out https://lumarenne.com and https://corvellagrille.com
• Would like to keep somewhat of a rustic and patriotic look and feel like the site currently is. We mainly cater in barn weddings and we cater for a lot of veterans. Will be pushing more corporate catering next year and opening a restaurant.

```html
<!DOCTYPE html>
<html lang="en">
<head>
<meta charset="utf-8">
<title>Weddings | Hollow Oak Smoke</title>
<link href="https://fonts.googleapis.com/css2?family=Roboto+Slab:wght@400;700&family=Roboto+Condensed:wght@700&family=Open+Sans:wght@400&display=swap" rel="stylesheet">
<style>
:root{
  --red:#ec1f27;
  --blue:#3176b5;
  --navy:#1f4f96;
  --white:#ffffff;
  --wood-dark:#3a2418;
  --wood-mid:#5a3a26;
  --cream:#f5f2ec;
  --cream-band:#e9e7e4;
  --text:#3b3b3b;
}
*{margin:0;padding:0;box-sizing:border-box}
html,body{width:766px;height:1200px;overflow:hidden;background:var(--cream)}
.page{position:relative;width:766px;height:1200px;overflow:hidden;background:var(--cream);font-family:"Open Sans",sans-serif}
.site-header{position:absolute;left:0;top:0;width:766px;height:74px;background:linear-gradient(180deg,#2c1a10,var(--wood-mid) 55%,#2c1a10)}
.brand{position:absolute;left:78px;top:8px;width:116px;height:116px;border-radius:50%;background:var(--white);border:5px solid #cfd3d8;display:flex;align-items:center;justify-content:center;text-align:center;z-index:3}
.brand span{font-family:"Roboto Slab",serif;font-weight:700;font-size:15px;line-height:1.1;color:var(--red)}
.social{position:absolute;top:13px;display:flex;gap:5px;left:611px}
.social span{width:22px;height:22px;border-radius:50%;border:1.5px solid var(--white)}
.main-nav{position:absolute;top:44px;left:219px;display:flex;gap:12px}
.main-nav a,.footer-nav a{font-family:"Roboto Condensed",sans-serif;font-weight:700;font-size:10px;color:var(--white);text-decoration:none;letter-spacing:.1px}
.main-nav a.current{color:var(--red)}
.hero{position:absolute;left:0;top:74px;width:766px;height:290px;background:linear-gradient(180deg,#ece8df 0%,#dfe6ea 40%,#7fa3bd 75%,#e7e3da 100%)}
.hero-title{position:absolute;top:166px;left:0;width:766px;text-align:center;font-family:"Roboto Slab",serif;font-weight:700;font-size:31px;color:var(--white);letter-spacing:.5px;text-shadow:0 1px 3px rgba(0,0,0,.25)}
.hero-curve{position:absolute;left:0;top:300px}
.page-title{position:absolute;top:346px;left:0;width:766px;text-align:center;font-family:"Roboto Slab",serif;font-weight:700;font-size:21px;color:var(--red)}
.band{position:absolute;left:0;top:580px;width:766px;height:256px;background:var(--cream-band)}
.event{position:absolute;width:340px}
.event h2{font-family:"Roboto Slab",serif;font-weight:400;font-size:16px;color:var(--navy);margin-bottom:14px}
.event p{font-size:8.2px;line-height:16px;color:var(--text);margin-bottom:9px}
.photo{position:absolute;width:233px;height:154px}
.photo-1{left:458px;top:410px;background:linear-gradient(180deg,#e6e9ea 0%,#d6dadc 55%,#d7a5d3 78%,#ece6ee 100%)}
.photo-2{left:88px;top:642px;background:linear-gradient(180deg,#f2f4f4 0%,#d9e2e6 40%,#a9b58c 70%,#ede9cc 100%)}
.photo-3{left:461px;top:877px;background:linear-gradient(180deg,#f3e3dc 0%,#d99a86 35%,#e7cfc6 65%,#ede6ee 100%)}
.site-footer{position:absolute;left:0;top:1068px;width:766px;height:132px}
.badge{position:absolute;left:353px;top:1076px;width:62px;height:62px;border-radius:50%;background:#5bb5e0;border:2px solid var(--white)}
.footer-nav{position:absolute;top:1148px;left:0;width:766px;display:flex;justify-content:center;gap:12px}
.copyright{position:absolute;top:1170px;left:0;width:766px;text-align:center;font-size:8px;color:#d8cfc6}
</style>
</head>
<body>
<div class="page">
  <div class="hero" role="img" aria-label="White gazebo with draped curtains overlooking the sea"></div>
  <h1 class="hero-title">WEDDINGS</h1>

  <header class="site-header">
    <nav class="main-nav">
      <a href="#">HOME</a><a href="#">MENU</a><a href="#">PHOTO GALLERY</a><a href="#">CORPORATE CATERING</a><a class="current" href="#">WEDDINGS</a><a href="#">VETERAN EVENTS</a><a href="#">CONTACT</a>
    </nav>
    <div class="social" aria-label="Social links"><span></span><span></span><span></span></div>
  </header>
  <div class="brand"><span>Hollow<br>Oak<br>Smoke</span></div>

  <svg class="hero-curve" width="766" height="70" viewBox="0 0 766 70" aria-hidden="true">
    <path d="M0 62 Q383 -10 766 62 L766 70 L0 70Z" fill="var(--cream)"/>
    <path d="M150 32 Q383 0 616 32" fill="none" stroke="var(--navy)" stroke-width="3"/>
    <path d="M0 62 Q383 -10 766 62" fill="none" stroke="var(--cream)" stroke-width="2"/>
  </svg>

  <h2 class="page-title">WEDDINGS</h2>
  <div class="band"></div>

  <section class="event" style="left:86px;top:406px">
    <h2>Event Tittle here</h2>
    <p>Fusce ultricies orci ac feugiat suscipit leo massa sodales velit et scelerisque mi tortor at ipsum cligula augue bibendum accumsan vestibulum ut commodo a mi Morbi ornare gravida elit Integer congue augue et malesuada iaculis</p>
    <p>ipsum dui aliquet felis at cursus magna nisl nec elit Praesent elementum elit at tellus nec ultricies sit amet porttitor mattis enim In massa libero interdum nec interdum vel blandit sed nulla In ullamcorper est eget tempor cursus neque mi consec</p>
  </section>
  <div class="photo photo-1" role="img" aria-label="Wedding head table decorated with pink flowers"></div>

  <div class="photo photo-2" role="img" aria-label="Outdoor ceremony aisle lined with white flowers and draped arch"></div>
  <section class="event" style="left:351px;top:638px">
    <h2>Event Tittle here</h2>
    <p>Fusce ultricies orci ac feugiat suscipit leo massa sodales velit et scelerisque mi tortor at ipsum cligula augue bibendum accumsan vestibulum ut commodo a mi Morbi ornare gravida elit Integer congue augue et malesuada iaculis</p>
    <p>ipsum dui aliquet felis at cursus magna nisl nec elit Praesent elementum elit at tellus nec ultricies sit amet porttitor mattis enim In massa libero interdum nec interdum vel blandit sed nulla In ullamcorper est eget tempor cursus neque mi consec</p>
  </section>

  <section class="event" style="left:89px;top:873px">
    <h2>Event Tittle here</h2>
    <p>Fusce ultricies orci ac feugiat suscipit leo massa sodales velit et scelerisque mi tortor at ipsum cligula augue bibendum accumsan vestibulum ut commodo a mi Morbi ornare gravida elit Integer congue augue et malesuada iaculis</p>
    <p>ipsum dui aliquet felis at cursus magna nisl nec elit Praesent elementum elit at tellus nec ultricies sit amet porttitor mattis enim In massa libero interdum nec interdum vel blandit sed nulla In ullamcorper est eget tempor cursus neque mi consec</p>
  </section>
  <div class="photo photo-3" role="img" aria-label="Reception hall with candelabra centerpiece and set tables"></div>

  <footer class="site-footer">
    <svg width="766" height="132" viewBox="0 0 766 132" aria-hidden="true">
      <defs>
        <linearGradient id="wood" x1="0" y1="0" x2="0" y2="1">
          <stop offset="0" stop-color="#4a2e1d"/>
          <stop offset=".5" stop-color="#5e3c27"/>
          <stop offset="1" stop-color="#2c1a10"/>
        </linearGradient>
      </defs>
      <path d="M0 0 Q383 80 766 0 L766 132 L0 132Z" fill="url(#wood)"/>
      <path d="M0 0 Q383 80 766 0" fill="none" stroke="var(--red)" stroke-width="3"/>
    </svg>
  </footer>
  <div class="badge" aria-label="The Vow Loft listing badge"></div>
  <nav class="footer-nav">
    <a href="#">HOME</a><a href="#">MENU</a><a href="#">PHOTO GALLERY</a><a href="#">CORPORATE CATERING</a><a href="#">WEDDINGS</a><a href="#">VETERAN EVENTS</a><a href="#">CONTACT</a>
  </nav>
  <p class="copyright">© 2017 Company Name  All right reserved  Term of Use</p>
</div>
</body>
</html>
```